Colin Vardek Business card

Hey there, I’m hoping to have a business card designed. I’m in Real estate and just switched to a new Brokerage called: The Harbourline Property Group

The back could just be the company name maybe or whatever looks good!

I’ve attached some logos of our company and some cards my buddy had done up.

On the card:
Colin Vardek
colinvardek@mailora.com
587-412-9065
colinvardek.ca

Target Market(s)

Home buyers and sellers

Industry/Entity Type

Real Estate

Contact Information for Business Card

just looking for a cool and modern design with my picture on it. I like the idea of Black and red being used.

Requirements
Must have
• all the details provided. I'm open to anything. Just want a professional looking card.

```html
<!DOCTYPE html>
<html lang="en">
<head>
<meta charset="utf-8">
<title>Colin Vardek – Business Card</title>
<link rel="stylesheet" href="https://fonts.googleapis.com/css2?family=Poppins:wght@400;500;700&display=swap">
<style>
  :root {
    --stage: #222223;
    --card-black: #212024;
    --brand-red: #cc2139;
    --white: #ffffff;
    --foil: #ecb093;
    --photo-light: #e9e6e4;
    --photo-dark: #b9b3b1;
  }
  * { margin: 0; padding: 0; box-sizing: border-box; }
  html, body {
    width: 1200px; height: 780px; overflow: hidden;
    background: var(--stage);
    font-family: "Poppins", sans-serif;
  }
  .stage {
    position: relative; width: 1200px; height: 780px;
    display: flex; align-items: center; justify-content: center; gap: 40px;
  }
  .card {
    position: relative; width: 540px; height: 309px; overflow: hidden;
    box-shadow: 0 18px 40px rgba(0,0,0,.45);
  }

  /* Front */
  .card-front { background: var(--card-black); }
  .brand-mark {
    position: absolute; left: 255px; top: 48px;
    display: flex; align-items: center; gap: 10px;
    color: var(--white); font-weight: 700; font-size: 19px; line-height: 1.08;
    text-transform: uppercase; letter-spacing: .3px;
  }
  .brand-mark .dot {
    width: 14px; height: 14px; background: var(--brand-red); flex: none;
  }
  .info-band {
    position: absolute; left: 0; right: 0; top: 150px; height: 96px;
    background: var(--brand-red);
  }
  .agent {
    position: absolute; left: 30px; top: 22px; color: var(--white);
  }
  .agent-name { font-size: 24px; line-height: 1.1; font-weight: 400; white-space: nowrap; }
  .agent-name strong { font-weight: 700; }
  .agent-title { font-size: 12.5px; font-weight: 400; margin-top: 3px; }
  .agent-photo {
    position: absolute; left: 206px; top: 0;
    width: 96px; height: 96px; border-radius: 50%;
    border: 3px solid var(--card-black);
    background: linear-gradient(180deg, var(--photo-light) 0 60%, var(--photo-dark) 100%);
  }
  .contact-list {
    position: absolute; left: 318px; top: 24px; list-style: none;
    color: var(--white); font-size: 13px;
  }
  .contact-list li { display: flex; align-items: center; gap: 8px; height: 24px; white-space: nowrap; }
  .contact-list svg { width: 12px; height: 12px; flex: none; }
  .website {
    position: absolute; left: 30px; top: 262px;
    color: var(--brand-red); font-size: 14px;
  }

  /* Back */
  .card-back {
    background: var(--brand-red);
    display: flex; align-items: center; justify-content: center;
  }
  .back-name {
    color: var(--foil); font-weight: 700; font-size: 34px; line-height: 1.1;
    text-transform: uppercase; text-align: center; letter-spacing: .5px;
  }
</style>
</head>
<body>
  <main class="stage">
    <section class="card card-front" aria-label="Card front">
      <div class="brand-mark">
        <span class="dot"></span>
        <span>The Harbourline<br>Property Group</span>
      </div>

      <div class="info-band">
        <div class="agent">
          <p class="agent-name"><strong>Colin</strong> Vardek</p>
          <p class="agent-title">Managing Director</p>
        </div>
        <div class="agent-photo" role="img" aria-label="Portrait photo of Colin Vardek"></div>
        <ul class="contact-list">
          <li>
            <svg viewBox="0 0 24 24" aria-hidden="true"><path fill="#fff" d="M6.6 10.8a15.1 15.1 0 0 0 6.6 6.6l2.2-2.2c.3-.3.7-.4 1-.2 1.1.4 2.3.6 3.6.6.6 0 1 .4 1 1V20c0 .6-.4 1-1 1A17 17 0 0 1 3 4c0-.6.4-1 1-1h3.5c.6 0 1 .4 1 1 0 1.3.2 2.5.6 3.6.1.3 0 .7-.2 1z"/></svg>
            <span>587-412-9065</span>
          </li>
          <li>
            <svg viewBox="0 0 24 24" aria-hidden="true"><rect x="2" y="5" width="20" height="14" rx="2" fill="#fff"/><path d="M3 6l9 7 9-7" fill="none" stroke="#cc2139" stroke-width="2"/></svg>
            <span>colinvardek@mailora.com</span>
          </li>
        </ul>
      </div>

      <p class="website">www.colinvardek.ca</p>
    </section>

    <section class="card card-back" aria-label="Card back">
      <p class="back-name">The Harbourline<br>Property Group</p>
    </section>
  </main>
</body>
</html>
```